BOLD & MINIMALIST DESIGN NEEDED

We want a very bold but minimalistic business card design that is impactful and utilizes both sides of the business card. Our current logo is included for your use.

We want bold fonts and good use of negative space. We don't want the logo to overpower the design.

Target Market(s)

Professionals who are building new commercial buildings.

Industry/Entity Type

Construction

Contact Information for Business Card

Name, Title, email, office phone, cell phone, website

Font styles to use
Serif
Sans Serif

Requirements
Must have
• Bold design!

```html
<!DOCTYPE html>
<html lang="en">
<head>
<meta charset="utf-8">
<title>Ridgeline Business Card</title>
<link href="https://fonts.googleapis.com/css2?family=Montserrat:wght@400;500;600;800&display=swap" rel="stylesheet">
<style>
  :root {
    --green: #5a9b1e;
    --green-bright: #74b431;
    --black: #050505;
    --paper: #f1f1f0;
    --ink: #111111;
    --rule: #8a8a8a;
    --backdrop: #d4d4d4;
  }
  * { box-sizing: border-box; margin: 0; padding: 0; }
  html, body {
    width: 1200px; height: 900px; overflow: hidden;
    background: var(--backdrop);
    font-family: "Montserrat", sans-serif;
  }
  .canvas {
    width: 1200px; height: 900px;
    display: flex; align-items: center; justify-content: center; gap: 40px;
  }
  .card {
    width: 540px; height: 308px;
    position: relative;
    box-shadow: 0 10px 30px rgba(0,0,0,.18);
  }
  /* Back side */
  .card-back {
    background: var(--black);
    display: flex; align-items: center; justify-content: center; gap: 18px;
  }
  .card-back .mark-square {
    width: 34px; height: 34px; background: var(--green-bright);
  }
  .card-back .brand-name {
    color: var(--green-bright);
    font-weight: 800; font-size: 52px; letter-spacing: 1px;
    text-transform: uppercase;
  }
  /* Front side */
  .card-front {
    background: var(--paper);
    display: flex;
  }
  .front-brand {
    width: 48%;
    display: flex; align-items: center; justify-content: center; gap: 10px;
  }
  .front-brand .mark-square {
    width: 18px; height: 18px; background: var(--ink);
  }
  .front-brand .brand-name {
    color: var(--ink);
    font-weight: 800; font-size: 30px; letter-spacing: .5px;
    text-transform: uppercase;
  }
  .divider {
    width: 1px; background: var(--rule);
    margin: 48px 0 36px;
  }
  .front-details {
    flex: 1;
    padding: 48px 24px 0 30px;
  }
  .person-name {
    font-weight: 600; font-size: 24px; color: var(--ink);
    text-transform: uppercase; letter-spacing: .3px;
  }
  .person-title {
    font-weight: 500; font-size: 15px; color: var(--green-bright);
    margin-top: 2px;
  }
  .contact-list { list-style: none; margin-top: 26px; }
  .contact-list li {
    display: flex; align-items: center; gap: 10px;
    font-size: 13px; font-weight: 500; color: var(--ink);
    margin-bottom: 9px;
  }
  .contact-list svg { width: 14px; height: 14px; fill: var(--green); flex: none; }
</style>
</head>
<body>
<main class="canvas">
  <section class="card card-back" aria-label="Card back">
    <span class="mark-square"></span>
    <span class="brand-name">Ridgeline</span>
  </section>

  <section class="card card-front" aria-label="Card front">
    <div class="front-brand">
      <span class="mark-square"></span>
      <span class="brand-name">Ridgeline</span>
    </div>
    <div class="divider"></div>
    <div class="front-details">
      <h1 class="person-name">Dorin Vasko</h1>
      <p class="person-title">CEO</p>
      <ul class="contact-list">
        <li>
          <svg viewBox="0 0 24 24" aria-hidden="true"><path d="M3 6c0-1 1-2 2-2h14c1 0 2 1 2 2v2h-5V6H8v2H3zm2 4h14l1 10H4zm7 2a3 3 0 100 6 3 3 0 000-6z"/></svg>
          <span>555 014 237</span>
        </li>
        <li>
          <svg viewBox="0 0 24 24" aria-hidden="true"><path d="M6.6 10.8a15 15 0 006.6 6.6l2.2-2.2c.3-.3.7-.4 1-.2 1.1.4 2.3.6 3.6.6.6 0 1 .4 1 1V20c0 .6-.4 1-1 1A17 17 0 013 4c0-.6.4-1 1-1h3.5c.6 0 1 .4 1 1 0 1.3.2 2.5.6 3.6.1.3 0 .7-.2 1z"/></svg>
          <span>555 014 237</span>
        </li>
        <li>
          <svg viewBox="0 0 24 24" aria-hidden="true"><path d="M2 5h20v14H2zm2 2v.5l8 5 8-5V7l-8 5z"/></svg>
          <span>info@ridgeline.com</span>
        </li>
        <li>
          <svg viewBox="0 0 24 24" aria-hidden="true"><path d="M12 2a10 10 0 100 20 10 10 0 000-20zm6.9 9h-3a15 15 0 00-1.3-6A8 8 0 0118.9 11zM12 4c.9 1.2 1.7 3.8 1.9 7h-3.8c.2-3.2 1-5.8 1.9-7zM9.4 5a15 15 0 00-1.3 6h-3A8 8 0 019.4 5zM5.1 13h3a15 15 0 001.3 6A8 8 0 015.1 13zm6.9 7c-.9-1.2-1.7-3.8-1.9-7h3.8c-.2 3.2-1 5.8-1.9 7zm2.6-1a15 15 0 001.3-6h3a8 8 0 01-4.3 6z"/></svg>
          <span>www.ridgeline.com</span>
        </li>
      </ul>
    </div>
  </section>
</main>
</body>
</html>
```